Unique Banner Design for weight loss project

We need a banner set for an online coaching program for weight loss. The following sizes are needed:
400x400
180x150
200x600
120x600
160x600
468x60
728x90
336x280
234x60
250x250
300x250
125x125

Here is the text:

1 verbotenes Lebensmittel, das du niemals essen darfst.

subhead: Verliere täglich etwas Bauchfett, indem du dieses 1 alltägliche Lebensmittel meidest.

***important: The Banner and image should be looked "hand drawn" LIKE the examples. For the image please DONT USE A BANANA. you can use one of the following veggies/fruits (of course hand drawn like the examples):

-cucumber
-potato
-Corncob
-zucchini
Updates

Reason: Wir haben bereits einen Sieger für unser Projekt. Dieser sollte lediglich noch 1-2 kleine Änderungen am Design vornehmen, dann wird der Designer ausgewählt.

Target Market(s)

weight loss, diet, nutrition

Industry/Entity Type

Weight

Requirements
Must have
• Here is the text:
• 1 verbotenes Lebensmittel, das du niemals essen darfst.
• subhead: Verliere täglich etwas Bauchfett, indem du dieses 1 alltägliche Lebensmittel meidest.
• ***important: The Banner and image should be looked "hand drawn" LIKE the examples. For the image please DONT USE A BANANA. you can use one of the following veggies/fruits (of course hand drawn like the examples):
• -cucumber
• -potato
• -Corncob
• -zucchini
Nice to have
• animated banner like "someone is eating the food" (see one of the examples)
Should not have
• NO strong call to action like click here or anyone else!

```html
<!DOCTYPE html>
<html lang="de">
<head>
<meta charset="utf-8">
<title>1 verbotenes Lebensmittel – Banner</title>
<link rel="stylesheet" href="https://fonts.googleapis.com/css2?family=Amatic+SC:wght@700&family=PT+Sans:ital,wght@1,400&display=swap">
<style>
  :root {
    --wood-base: #1b1b1b;
    --wood-light: #232323;
    --wood-seam: #0c0c0c;
    --banner-bg: #ffffff;
    --headline-green: #3f7d22;
    --subhead-brown: #b27636;
    --potato-light: #f1d9a4;
    --potato-mid: #d9b06a;
    --potato-dark: #b98a45;
  }
  * { margin: 0; padding: 0; box-sizing: border-box; }
  html, body {
    width: 1200px;
    height: 1200px;
    overflow: hidden;
    background: var(--wood-base);
  }
  .stage {
    position: relative;
    width: 1200px;
    height: 1200px;
    background:
      repeating-linear-gradient(90deg,
        var(--wood-seam) 0px, var(--wood-seam) 3px,
        var(--wood-light) 3px, var(--wood-base) 30px,
        var(--wood-light) 55px, var(--wood-base) 85px),
      var(--wood-base);
  }
  .banner {
    position: absolute;
    left: 367px;
    top: 405px;
    width: 467px;
    height: 389px;
    background: var(--banner-bg);
    overflow: hidden;
  }
  .banner__visual {
    position: absolute;
    left: 57px;
    top: 11px;
    width: 356px;
    height: 215px;
    border-radius: 50%;
    background: radial-gradient(ellipse at 45% 40%, var(--potato-light) 0%, var(--potato-mid) 60%, var(--potato-dark) 100%);
  }
  .banner__headline {
    position: absolute;
    left: 0;
    top: 232px;
    width: 100%;
    text-align: center;
    font-family: "Amatic SC", cursive;
    font-weight: 700;
    font-size: 51px;
    line-height: 43px;
    color: var(--headline-green);
  }
  .banner__subhead {
    position: absolute;
    left: 0;
    top: 327px;
    width: 100%;
    text-align: center;
    font-family: "PT Sans", sans-serif;
    font-style: italic;
    font-size: 19px;
    line-height: 24px;
    color: var(--subhead-brown);
  }
</style>
</head>
<body>
  <main class="stage">
    <section class="banner">
      <div class="banner__visual" role="img" aria-label="Illustration: zwei ganze Kartoffeln und eine in Scheiben geschnittene Kartoffel mit grünen Blättern"></div>
      <h1 class="banner__headline">1 verbotenes Lebensmittel,<br>das du niemals essen darfst</h1>
      <p class="banner__subhead">Verliere täglich etwas Bauchfett, indem<br>du dieses 1 alltägliche Lebensmittel meidest</p>
    </section>
  </main>
</body>
</html>
```